elegant beautiful Hang tag for a novelty makeup towel

It's a black hand towel in the shape of a little black dress. it is called PETAL CHARM TOWEL, it is a CLEAN SLATE MAKEUP TOWEL. (doesn't show our makeup stains) Made in USA

Target Market(s)

ALL Women , Makeup artists, novelty THIS WILL BE IN THE HALVERGATE STORES AND KESTRELMOOR STORES.

Industry/Entity Type

Makeup

Contact Information for Business Card

I actually need a hang tag for a homemade handmade towel. I have a logo that I want on the tag and know what we want to say on it, on back needs to say "The essential to every girl's wardrobe. So when the little black dress comes off, our PETAL CHARM TOWEL is there to help you wash your day away. Include website www.petalcharmtowel.com OH INCLUDE TM (trademark sign next to logo please. Also, in small print on back from the makers of THE ORIGINAL CLEAN SLATE MAKEUP TOWEL. handmade in USA. also CLEAN SLATE MAKEUP TOWEL IN big font on front under logo sign with light colored pink lips after 'CLEAN SLATE" but have no idea about fonts, graphics, placement or design. Want it classy, elegant, girly! COLORS LIGHT BEIGER BACKGROUND WITH BLACK WRITING/ DESIGNS

Font styles to use
Serif
Decorative
Script

Colors
fff3d1

Requirements
Must have
• Black cream girly , also state in big writing that it's a " clean slate makeup towel" with a tiny light pink lip between the show and makeup. Include www.petalcharmtowel.com Brightwater Fenn, LLC
Nice to have
• Perhaps an outline of a little black dress. A black scroll edge of some sort around card. Classy

```html
<!DOCTYPE html>
<html lang="en">
<head>
<meta charset="utf-8">
<title>Petal Charm Towel – Hang Tag</title>
<link rel="stylesheet" href="https://fonts.googleapis.com/css2?family=Aleo:wght@400;500&family=Montserrat:wght@600&display=swap">
<style>
  :root {
    --stage: #000000;
    --cream: #fff6d6;
    --ink: #2a2323;
    --lip-pink: #f4b8c4;
  }
  * { margin: 0; padding: 0; box-sizing: border-box; }
  html, body { width: 1200px; height: 1200px; overflow: hidden; background: var(--stage); }
  .canvas { position: relative; width: 1200px; height: 1200px; }

  .tag {
    position: absolute;
    background: var(--cream);
    border-radius: 24px;
    color: var(--ink);
  }
  .tag--front { left: 264px; top: 319px; width: 324px; height: 559px; }
  .tag--back  { left: 612px; top: 322px; width: 316px; height: 556px; }

  /* Front */
  .hero-art {
    position: absolute;
    left: 50px; top: 185px;
    width: 224px; height: 336px;
    border-radius: 40px 40px 90px 90px;
    background: linear-gradient(180deg, #f4e8c4 0%, #8a7c6e 38%, var(--ink) 60%);
  }
  .front-brand {
    position: absolute;
    left: 0; right: 0; top: 384px;
    text-align: center;
    font-family: "Montserrat", sans-serif;
    font-weight: 600;
    color: var(--cream);
  }
  .front-brand__name {
    font-size: 25px;
    line-height: 28px;
    letter-spacing: 1px;
  }
  .front-brand__name sup { font-size: 7px; vertical-align: 14px; letter-spacing: 0; }
  .front-brand__tagline {
    display: flex;
    justify-content: center;
    align-items: center;
    gap: 4px;
    margin-top: 7px;
    font-size: 8px;
    letter-spacing: 0.8px;
  }
  .lip-mark {
    display: inline-block;
    width: 9px; height: 5px;
    border-radius: 50%;
    background: var(--lip-pink);
  }

  /* Back */
  .back-copy {
    position: absolute;
    left: 0; right: 0;
    text-align: center;
    font-family: "Aleo", serif;
  }
  .back-copy p { font-size: 15px; line-height: 18px; }
  .intro { top: 140px; }
  .intro .lead-in { margin-bottom: 12px; }
  .wordmark {
    margin: 10px 0 8px;
    font-family: "Montserrat", sans-serif;
    font-weight: 600;
    font-size: 21px;
    letter-spacing: 2px;
  }
  .wordmark sup { font-size: 7px; letter-spacing: 0; }
  .back-emblem {
    position: absolute;
    left: 115px; top: 352px;
    width: 86px; height: 30px;
    border-radius: 15px;
    background: var(--ink);
  }
  .maker { top: 458px; }
  .maker .maker__name, .maker .maker__site { font-size: 12.5px; line-height: 19px; }
  .maker .maker__origin { font-size: 14.5px; line-height: 22px; }
</style>
</head>
<body>
<main class="canvas">
  <section class="tag tag--front">
    <div class="hero-art" role="img" aria-label="Illustration of a little black dress in dark ink"></div>
    <div class="front-brand">
      <div class="front-brand__name">PETAL<br>CHARM<br>TOWEL<sup>™</sup></div>
      <div class="front-brand__tagline">
        <span>CLEAN SLATE</span>
        <span class="lip-mark" role="img" aria-label="Light pink lips"></span>
        <span>MAKEUP TOWEL</span>
      </div>
    </div>
  </section>

  <section class="tag tag--back">
    <div class="back-copy intro">
      <p class="lead-in">The essential to every girl's wardrobe.</p>
      <p>So when the little black dress<br>comes off, our</p>
      <div class="wordmark">PETAL CHARM TOWEL<sup>™</sup></div>
      <p>is there to help you wash your day away</p>
    </div>
    <div class="back-emblem" role="img" aria-label="Small decorative emblem in dark ink"></div>
    <div class="back-copy maker">
      <p class="maker__name">Brightwater Fenn, LLC</p>
      <p class="maker__site">www.petalcharmtowel.com</p>
      <p class="maker__origin">handmade in USA</p>
    </div>
  </section>
</main>
</body>
</html>
```